OpenHarbor Yoga Website Design

Business Logo - attached
5 pages being:
Home
About
Classes
Blog
Contact

Would like Scrolling webpage and yoga symbols to be used.

Must have's being:
Easy to navigate, Text needs to be able to be edited/updated, Enquire Now Links, More Information Links, be a secure site, SEO,

Please refer to attached document for the information for the body of the website.

Target Market(s)

Educators, Community Service, Health and Wellbeing, Mental Health

Industry/Entity Type

Yoga

Coding

Coded - Design and coding required

Number of Pages Required

5+ page

Font styles to use
Other font styles liked:
• Bella Bold BC

Colors
0094D4
00A9DD
6FCCEA
C7EBF8
E9F6FB
6B429C
8869AF
B7A5CE
E3DAEB
F3F0F8

Requirements
Must have
• Easy to navigate, Text needs to be able to be edited/updated, Enquire Now Links, More Information Links, be a secure site, SEO,
Nice to have
• Scrolling webpage, yoga symbols

```html
<!DOCTYPE html>
<html lang="en">
<head>
<meta charset="utf-8">
<title>OpenHarbor Yoga</title>
<link rel="stylesheet" href="https://fonts.googleapis.com/css2?family=Montserrat:wght@400;500;600&family=Yellowtail&display=swap">
<style>
:root{
  --blue:#0094D4;
  --blue-2:#00A9DD;
  --purple:#6B429C;
  --purple-2:#8869AF;
  --lilac:#B7A5CE;
  --ink:#222222;
  --bar:#1e1e1e;
  --navy:#0b1620;
  --white:#ffffff;
}
*{box-sizing:border-box;margin:0;padding:0}
html,body{width:1200px;height:4065px;overflow:hidden}
body{position:relative;background:var(--white);font-family:"Montserrat",sans-serif;color:var(--ink)}
.abs{position:absolute}
.script{font-family:"Yellowtail",cursive;font-weight:400}
.btn{position:absolute;display:flex;align-items:center;justify-content:center;background:var(--blue);color:var(--white);border-radius:22px;font-size:15px;font-weight:500;text-decoration:none}

/* header */
.site-header{position:absolute;left:0;top:0;width:1200px;height:147px;background:var(--bar)}
.brand{position:absolute;left:114px;top:58px;display:flex;align-items:center;gap:10px;color:var(--lilac);font-size:17px;font-weight:500}
.brand-dot{width:22px;height:22px;border-radius:50%;background:var(--purple-2)}
.nav a{position:absolute;top:64px;color:var(--white);font-size:17px;text-decoration:none}

/* hero */
.hero-photo{position:absolute;left:0;top:147px;width:1200px;height:683px;
  background:radial-gradient(ellipse at 35% 25%,#8a8296 0%,#5a5266 35%,#2c2735 70%,#1b1822 100%)}
.hero-title{left:114px;top:360px;font-size:64px;color:var(--white)}
.hero-text{left:114px;top:461px;width:420px;font-size:16px;line-height:29px;color:#eeeaf2}

/* welcome */
.welcome{position:absolute;left:0;top:780px;width:1200px;height:581px;
  background:radial-gradient(ellipse at 50% 55%,#1c2a36 0%,#0d1a24 55%,#07111a 100%)}
.welcome-title{left:0;width:1200px;top:905px;text-align:center;font-size:40px;color:var(--white)}
.welcome-text{left:114px;width:974px;font-size:16.5px;line-height:29px;color:var(--white);text-align:justify;text-align-last:center}

/* benefits */
.section-title{font-size:40px;color:#111}
.body-text{font-size:16px;line-height:29px;color:#333}
.photo{position:absolute}
.benefit-title{font-size:32px;color:#111}
.benefit-list{position:absolute;list-style:none;font-size:16px;line-height:29px;color:#333}
.benefit-list li{display:flex;align-items:center;gap:14px}
.benefit-list li::before{content:"";width:8px;height:8px;border-radius:50%;background:var(--blue);flex:none}

/* contact */
.contact-card{position:absolute;left:44px;top:2968px;width:1112px;height:597px;border:4px solid #7b3fe0;border-radius:36px;overflow:hidden;
  background:linear-gradient(120deg,#3a3a40 0%,#26262b 45%,#1d1d22 100%)}
.contact-title{left:114px;top:3030px;font-size:36px;color:var(--white)}
.contact-text{left:114px;top:3100px;width:440px;font-size:16px;line-height:27.5px;color:var(--white)}
.field{position:absolute;left:635px;width:477px;height:63px;background:var(--white);border:1px solid #d9d9d9;padding-left:31px;display:flex;align-items:center;font-size:18px;color:#8a8a8a}

/* footer */
.footer{position:absolute;left:0;top:3680px;width:1200px;height:334px}
.footer-brand{left:118px;top:3872px;display:flex;align-items:center;gap:10px;color:var(--lilac);font-size:18px;font-weight:500}
.footer-links a{position:absolute;left:343px;color:var(--white);font-size:15px;text-decoration:none}
.footer-rule{position:absolute;top:3834px;width:1px;height:118px;background:#6a6a6a}
.footer-info{color:var(--white);font-size:16px;line-height:34px}
.social{position:absolute;top:3910px;width:28px;height:28px;border-radius:50%}
.copyright{position:absolute;left:0;top:4014px;width:1200px;height:51px;background:var(--blue);color:var(--white);font-size:12.5px;display:flex;align-items:center;justify-content:center}
</style>
</head>
<body>

<header class="site-header">
  <div class="brand"><span class="brand-dot"></span>OpenHarbor Yoga</div>
  <nav class="nav">
    <a style="left:662px">Home</a>
    <a style="left:753px">About</a>
    <a style="left:846px">Classes</a>
    <a style="left:947px">Blog</a>
    <a style="left:1026px">Contact</a>
  </nav>
</header>

<div class="hero-photo" role="img" aria-label="Silhouette of a woman meditating by the sea at dusk with flowing purple ribbons"></div>
<h1 class="abs script hero-title">Welcome To OpenHarbor Yoga</h1>
<p class="abs hero-text">Lorem ipsum dolor sit amet, consectetur adipiscing elit, sed do ut labore et dolore magna aliqua.</p>
<a class="btn" style="left:114px;top:546px;width:131px;height:41px">Enquire Now</a>

<section class="welcome" role="img" aria-label="Woman seated cross-legged with arms outstretched in a dark studio"></section>
<svg class="abs" style="left:0;top:690px" width="1200" height="140" viewBox="0 0 1200 140">
  <path d="M0 95 C150 70 300 120 520 115 C700 110 760 60 900 55 C1000 50 1080 40 1200 20 L1200 140 L0 140 Z" fill="#0c1822"/>
  <path d="M0 95 C150 70 300 120 520 115 C700 110 760 60 900 55 C1000 50 1080 40 1200 20" fill="none" stroke="#7b3fe0" stroke-width="6"/>
</svg>
<h2 class="abs script welcome-title">Welcome to OpenHarbor Yoga...</h2>
<p class="abs welcome-text" style="top:989px">OpenHarbor Yoga believe that you are never too young to benefit from and fall in love with yoga. My aim is to EMPOWER kids and teens to thrive by teaching life skills in Yoga, Mindfulness and Breathing techniques to deal with daily challenges and big emotions.</p>
<p class="abs welcome-text" style="top:1105px">OpenHarbor Yoga gives kids an opportunity to enjoy and experience yoga for themselves and primarily focuses on programs for Schools, Pre Schools and Early Learning Centres, Private Classes, Sporting Clubs, Martial Arts Schools, Scout Groups and Occupational Therapy Centres just to name a few. All classes are age appropriate and encourage children's natural drive to learn, move, and be creative.</p>
<a class="btn" style="left:519px;top:1255px;width:163px;height:40px">More Information</a>

<h2 class="abs script section-title" style="left:114px;top:1440px">Benefits of Yoga...</h2>
<p class="abs body-text" style="left:114px;top:1520px;width:960px">The benefits of yoga can last a lifetime. It is my aim &amp; passion to introduce yoga to kids of all ages and backgrounds so that they can not only experience the benefits of yoga but fall in love with the practice.</p>
<p class="abs" style="left:114px;top:1608px;font-size:18px;font-weight:500;color:#111">Yoga benefits include:</p>

<div class="photo" style="left:114px;top:1708px;width:486px;height:255px;background:linear-gradient(135deg,#c9ced4,#aeb4bb)" role="img" aria-label="Woman in a high lunge pose with arms raised"></div>
<h3 class="abs script benefit-title" style="left:636px;top:1682px">Healthy Bodies:</h3>
<ul class="benefit-list" style="left:636px;top:1738px">
  <li>Develops strong, flexible and healthy bodies</li>
  <li>Promotes spinal alignment and good posture</li>
  <li>Builds energy and stamina</li>
  <li>Improves internal physical function - organs, digestion,</li>
  <li>elimination, circulation, and blood flow.</li>
  <li>Helps breathing and lung capacity</li>
  <li>Teaches the enjoyment of movement</li>
  <li>Works the 'whole' body</li>
</ul>

<h3 class="abs script benefit-title" style="left:120px;top:2028px">Healthy Minds</h3>
<ul class="benefit-list" style="left:120px;top:2085px">
  <li>Cultivates confidence and self-esteem</li>
  <li>Develops concentration and attention</li>
  <li>Clears the mind for better clarity and decision making</li>
  <li>Helps relax and sleep better</li>
  <li>Calms the nervous system</li>
  <li>Learns to cope with stressful situations</li>
  <li>Balances emotions</li>
</ul>
<div class="photo" style="left:600px;top:2048px;width:491px;height:245px;background:linear-gradient(135deg,#e4e2de,#b9c3cc 55%,#4aa3d8)" role="img" aria-label="Two people meditating cross-legged on blue mats in a living room"></div>

<div class="photo" style="left:114px;top:2400px;width:491px;height:245px;background:linear-gradient(180deg,#8a8f9a 0%,#c79a6a 60%,#d9822f 85%,#2a2420 100%)" role="img" aria-label="Silhouette of a woman in a standing bow pose at sunset beside stacked stones"></div>
<h3 class="abs script benefit-title" style="left:638px;top:2383px">Healthy Spirits</h3>
<ul class="benefit-list" style="left:638px;top:2437px">
  <li>Fosters creativity, expression and imagination</li>
  <li>Cultivates kindness to themselves and others</li>
  <li>Cultivates respect for self and others</li>
  <li>Builds balance and inner quiet</li>
  <li>Builds inner strength and resilience</li>
  <li>Teaches self-awareness</li>
  <li>Focuses on positive self-talk</li>
</ul>

<p class="abs body-text" style="left:114px;top:2710px;width:972px;text-align:center">OpenHarbor Yoga combines all the benefits of traditional yoga and a lot of fun!<br>We play games and practice engaging flows which get our bodies moving, then we take a quiet moment to be still and calm as we focus on our breathing.</p>
<p class="abs body-text" style="left:114px;top:2827px;width:972px;text-align:center">OpenHarbor Yoga Kids will learn that relaxation is just as important as moving their bodies, and the exercises which they learn in class can easily be repeated at any time in their busy day to feel calm and grounded.</p>

<section class="contact-card" role="img" aria-label="Hands unrolling a grey yoga mat"></section>
<h2 class="abs script contact-title">Contact Us</h2>
<p class="abs contact-text">Lorem ipsum dolor sit amet, consectetur adipiscing elit, sed do eiusmod tempor incididunt ut labore et dolore magna aliqua. Quis ipsum suspendisse ultrices gravida. Risus commodo viverra maecenas accumsan lacus vel facilisis.</p>
<a class="btn" style="left:112px;top:3265px;width:186px;height:41px;font-size:16px">Learn More</a>
<div class="field" style="top:3032px">Name</div>
<div class="field" style="top:3112px">Email</div>
<div class="field" style="top:3193px">Phone</div>
<div class="field" style="top:3273px">Subject</div>
<div class="field" style="top:3354px">Message</div>
<a class="btn" style="left:635px;top:3450px;width:186px;height:41px;font-size:16px">Get In Touch</a>

<svg class="abs" style="left:0;top:3660px" width="1200" height="360" viewBox="0 0 1200 360">
  <path d="M0 42 C120 20 230 10 330 22 C480 40 560 70 700 90 C850 112 960 130 1060 112 C1120 102 1160 96 1200 98 L1200 360 L0 360 Z" fill="var(--bar)"/>
  <path d="M0 42 C120 20 230 10 330 22 C480 40 560 70 700 90 C850 112 960 130 1060 112 C1120 102 1160 96 1200 98" fill="none" stroke="#7b3fe0" stroke-width="7"/>
</svg>
<div class="abs footer-brand"><span class="brand-dot"></span>OpenHarbor Yoga</div>
<nav class="footer-links">
  <a style="top:3832px">Home</a>
  <a style="top:3861px">About</a>
  <a style="top:3890px">Classes</a>
  <a style="top:3919px">Blog</a>
  <a style="top:3948px">Contact</a>
</nav>
<span class="footer-rule" style="left:499px"></span>
<svg class="abs" style="left:556px;top:3832px" width="14" height="20" viewBox="0 0 14 20"><path d="M7 0C3 0 0 3 0 7c0 5 7 13 7 13s7-8 7-13C14 3 11 0 7 0zm0 10a3 3 0 110-6 3 3 0 010 6z" fill="var(--blue-2)"/></svg>
<p class="abs footer-info" style="left:584px;top:3824px">#1, Sample Street,<br>Sample City, USA<br>377646</p>
<span class="footer-rule" style="left:821px"></span>
<svg class="abs" style="left:860px;top:3832px" width="16" height="16" viewBox="0 0 24 24"><path d="M6.6 10.8a15 15 0 006.6 6.6l2.2-2.2c.3-.3.7-.4 1-.2 1.1.4 2.3.6 3.6.6.6 0 1 .4 1 1V20c0 .6-.4 1-1 1A17 17 0 013 4c0-.6.4-1 1-1h3.5c.6 0 1 .4 1 1 0 1.3.2 2.5.6 3.6.1.3 0 .7-.2 1z" fill="var(--blue-2)"/></svg>
<p class="abs footer-info" style="left:887px;top:3824px">+1 888 8888 8888</p>
<svg class="abs" style="left:858px;top:3870px" width="18" height="13" viewBox="0 0 18 13"><rect width="18" height="13" rx="1.5" fill="var(--blue-2)"/><path d="M1 1l8 6 8-6" fill="none" stroke="var(--bar)" stroke-width="1.5"/></svg>
<p class="abs footer-info" style="left:887px;top:3862px">hello@openharboryoga.com</p>
<span class="social" style="left:856px;background:var(--purple-2)"></span>
<span class="social" style="left:897px;background:var(--blue)"></span>

<footer class="copyright">© copyrights 2023 OpenHarbor Yoga | All Rights Reserved</footer>

</body>
</html>
```